Design a refer a friend Flyer (French & English)
Flyer Title:
Main Title: "Refer a Friend & Receive a Free Electric Toothbrush!"
Bold and clear, centered at the top.
Use a clean and modern font.
Color: White text on a vivid green background for maximum contrast and readability.
Visual Focus:
Toothbrush Image: Place a high-quality image of the Dentiva Max 300 Electric Toothbrush in the center of the flyer.
Include a small price tag with “Value of $50” near the toothbrush to highlight the reward.
Simple Message:
Text: "Refer a friend to Centre Dentaire Lac-Ombré. When they book and attend their appointment, you get a free electric toothbrush, and they receive a special gift!"
Straightforward and easy to understand.
Placed below the image of the toothbrush.
Referral Process:
3 Easy Steps:
Refer a Friend
They Book and Come to Their Appointment
Receive Your Free Electric Toothbrush
Use simple, minimal icons to visually represent each step.
Keep the steps aligned horizontally or vertically for clarity.
Call to Action:
Text: "Start Referring Today!"
Place it in a button-like design in the vivid green color with bold, white text to make it stand out.
Contact Information:
Details:
Logo of Centre Dentaire Lac-Ombré.
Address: "42 Rue Valmonde Ouest, Suite 310".
Phone Number and Website: Positioned at the bottom for easy reference.
Color Scheme:
Use a vivid green background for the entire flyer, with white accents for text and icons to maintain a fresh, clean look.
Minimal clutter, focusing on clarity and the key elements: the toothbrush, the call to action, and contact information.
Clinic : www.cdlacombre.example
Attached is the brandbook, logo and inspo I made with AI.
French text will be provided.
Thank you,
Tarin

```html
<!DOCTYPE html>
<html lang="en">
<head>
<meta charset="utf-8">
<title>Refer a Friend Flyer</title>
<link rel="stylesheet" href="https://fonts.googleapis.com/css2?family=Montserrat:wght@500;600;700;900&family=Roboto:wght@500;700;900&family=Roboto+Condensed:wght@700;800&display=swap">
<style>
  :root{
    --green-top:#0b8f2c;
    --green-mid:#08701f;
    --green-deep:#04461a;
    --pane-dark:#033015;
    --white:#ffffff;
    --red:#e5100f;
    --ribbon:#c90d0d;
    --ink:#1f2b24;
    --charcoal:#262626;
    --step1:#0b4a22;
    --step2:#178a6a;
    --step3:#1b7fa6;
    --icon:#2a8a5a;
    --pedestal:#b9d9a4;
  }
  *{box-sizing:border-box;margin:0;padding:0}
  html,body{width:867px;height:1200px;overflow:hidden}
  body{font-family:"Montserrat",sans-serif;color:var(--white)}
  .flyer{
    position:relative;width:867px;height:1200px;overflow:hidden;
    background:linear-gradient(180deg,var(--green-top) 0%,var(--green-mid) 45%,var(--green-deep) 75%,#06601e 100%);
  }
  .product-pane{
    position:absolute;left:513px;top:259px;width:317px;height:772px;
    border-radius:0 0 160px 160px;
    background:linear-gradient(180deg,rgba(0,0,0,0) 0%,var(--pane-dark) 55%,rgba(3,48,21,.6) 100%);
  }
  .eyebrow{
    position:absolute;left:75px;top:48px;
    font-weight:500;font-size:31px;letter-spacing:5.4px;white-space:nowrap;
  }
  .headline{
    position:absolute;left:75px;top:104px;
    font-weight:900;font-size:85px;line-height:86px;letter-spacing:-1.5px;white-space:nowrap;
  }
  .headline .free{
    display:inline-block;background:var(--red);padding:0 8px 0 10px;margin-right:8px;line-height:82px;
  }
  .headline .line2{display:block;font-size:87px;margin-top:2px}
  .message{
    position:absolute;left:40px;width:405px;top:304px;text-align:center;
    font-size:20px;line-height:29px;font-weight:500;
  }
  .message strong{font-weight:700;font-size:21px;display:block;line-height:32px}
  .gift{
    position:absolute;left:93px;top:527px;width:297px;height:133px;
    border:3px solid var(--red);border-radius:26px;
    display:flex;align-items:center;justify-content:center;text-align:center;
    font-family:"Roboto",sans-serif;font-weight:900;font-size:46px;line-height:46px;padding-top:14px;
  }
  .gift-bow{
    position:absolute;left:118px;top:494px;width:250px;height:60px;
    background:radial-gradient(ellipse at center,#e0201a 0%,var(--ribbon) 55%,rgba(201,13,13,0) 75%);
  }
  .steps-title{
    position:absolute;left:63px;top:704px;
    font-family:"Roboto",sans-serif;font-weight:700;font-size:40px;letter-spacing:-.5px;
  }
  .step{
    position:absolute;top:773px;width:135px;height:111px;background:var(--white);border-radius:6px;
    color:var(--ink);font-family:"Roboto",sans-serif;font-weight:500;font-size:13.5px;line-height:17px;
    display:flex;align-items:center;gap:6px;padding:16px 4px 0 15px;
  }
  .step-tab{
    position:absolute;top:-15px;left:27px;width:82px;height:34px;border-radius:6px 6px 0 0;
    color:var(--white);font-weight:700;font-size:12px;display:flex;align-items:center;justify-content:center;
  }
  .step svg{flex:0 0 auto;width:26px;height:26px}
  .step-1{left:53px}.step-1 .step-tab{background:var(--step1)}
  .step-2{left:201px}.step-2 .step-tab{background:var(--step2)}
  .step-3{left:350px}.step-3 .step-tab{background:var(--step3)}
  .clinic-name{
    position:absolute;left:75px;top:918px;font-family:"Roboto",sans-serif;font-weight:700;color:var(--white);
    font-size:40px;line-height:44px;letter-spacing:-.5px;
  }
  .clinic-name span{display:block;font-size:16px;line-height:20px}
  .cta{
    position:absolute;left:0;top:1018px;width:496px;height:48px;background:var(--charcoal);
    border-radius:0 24px 24px 0;font-family:"Roboto",sans-serif;font-weight:700;font-size:27px;
    display:flex;align-items:center;padding-left:75px;letter-spacing:.2px;
  }
  .contact{
    position:absolute;left:71px;display:flex;align-items:center;gap:11px;font-size:20px;font-weight:500;
  }
  .contact svg{width:25px;height:25px}
  .contact-address{top:1083px}
  .contact-web{top:1120px}
  .value-badge{position:absolute;left:448px;top:452px;width:230px;height:230px}
  .value-text{
    position:absolute;left:448px;top:508px;width:230px;text-align:center;
    font-family:"Roboto Condensed",sans-serif;font-weight:800;line-height:1;
  }
  .value-text .label{font-size:33px;display:block}
  .value-text .amount{font-size:76px;display:block;margin-top:4px;letter-spacing:-1px}
  .value-text .amount sup{font-size:38px;vertical-align:26px}
  .product-photo{
    position:absolute;left:600px;top:340px;width:220px;height:880px;
    border-radius:110px 110px 40px 40px;
    background:
      radial-gradient(circle at 50% 90px,rgba(70,230,70,.55) 0,rgba(70,230,70,.15) 80px,rgba(0,0,0,0) 110px),
      linear-gradient(90deg,rgba(0,0,0,0) 30%,#1d1d1d 40%,#2a2a2a 55%,#151515 65%,rgba(0,0,0,0) 75%) center 40px/100% 740px no-repeat;
  }
  .pedestal{
    position:absolute;left:520px;top:1010px;width:347px;height:190px;
    background:linear-gradient(180deg,#e9f2e2 0%,var(--pedestal) 40%,#a7cf92 100%);
    border-radius:60% 60% 0 0/40% 40% 0 0;
  }
</style>
</head>
<body>
<main class="flyer">
  <div class="product-pane"></div>

  <p class="eyebrow">REFER A FRIEND &amp; RECEIVE A</p>
  <h1 class="headline"><span class="free">FREE</span>ELECTRIC<span class="line2">TOOTH BRUSH!</span></h1>

  <p class="message"><strong>Refer a friend to Centre Dentaire Lac-Ombré.</strong>When they book and attend their appointment, you get a free electric toothbrush, and receive a</p>

  <div class="gift">SPECIAL<br>GIFT!</div>
  <div class="gift-bow" role="img" aria-label="Red ribbon bow on top of the gift box"></div>

  <div class="pedestal" role="img" aria-label="Pale green round display pedestal"></div>
  <div class="product-photo" role="img" aria-label="Dentiva Max 300 black electric toothbrush with glowing green swirl around the brush head"></div>

  <svg class="value-badge" viewBox="0 0 230 230" aria-hidden="true">
    <polygon fill="var(--charcoal)" points="115,0 148,20 186,20 198,56 228,80 218,115 228,150 198,174 186,210 148,210 115,230 82,210 44,210 32,174 2,150 12,115 2,80 32,56 44,20 82,20"/>
    <circle cx="115" cy="115" r="96" fill="none" stroke="var(--white)" stroke-width="3"/>
  </svg>
  <div class="value-text"><span class="label">VALUE OF</span><span class="amount"><sup>$</sup>50</span></div>

  <h2 class="steps-title">3 EASY STEPS:</h2>

  <div class="step step-1">
    <div class="step-tab">STEP 1</div>
    <svg viewBox="0 0 26 26" fill="none" stroke="var(--icon)" stroke-width="1.4"><circle cx="13" cy="13" r="11.5"/><rect x="6" y="13" width="4" height="6"/><path d="M10 13l3-5v-2h2v5h4v8h-9"/></svg>
    <span>Refer a<br>Friend</span>
  </div>
  <div class="step step-2">
    <div class="step-tab">STEP 2</div>
    <svg viewBox="0 0 26 26" fill="none" stroke="var(--icon)" stroke-width="1.4"><rect x="2" y="5" width="17" height="15" rx="1"/><path d="M2 10h17M7 3v4M14 3v4M6 13h3M11 13h3M6 16h3"/><circle cx="20" cy="19" r="4.5"/><path d="M20 17v4M18 19h4"/></svg>
    <span>They Book and Come to Their Appointment</span>
  </div>
  <div class="step step-3">
    <div class="step-tab">STEP 3</div>
    <svg viewBox="0 0 26 26" fill="none" stroke="var(--step3)" stroke-width="1.4"><rect x="11" y="4" width="4" height="5" rx="1"/><rect x="10" y="9" width="6" height="16" rx="2"/><path d="M3 6c2-3 5-3 7-2M23 6c-2-3-5-3-7-2"/></svg>
    <span>Receive Your Free Electric Toothbrush</span>
  </div>

  <div class="clinic-name">Clinique Dentaire<span>Lac-Ombré</span></div>

  <div class="cta">START REFERRING TODAY!</div>

  <div class="contact contact-address">
    <svg viewBox="0 0 25 25"><circle cx="12.5" cy="12.5" r="12.5" fill="#11a442"/><path d="M12.5 5.5a4 4 0 0 0-4 4c0 3 4 7.5 4 7.5s4-4.5 4-7.5a4 4 0 0 0-4-4z" fill="var(--white)"/><circle cx="12.5" cy="9.5" r="1.5" fill="#11a442"/><ellipse cx="12.5" cy="18.5" rx="5" ry="1.3" fill="none" stroke="var(--white)" stroke-width="1"/></svg>
    <span>42 Rue Valmonde Ouest, Suite 310</span>
  </div>
  <div class="contact contact-web">
    <svg viewBox="0 0 25 25"><circle cx="12.5" cy="12.5" r="12.5" fill="#11a442"/><g fill="none" stroke="var(--white)" stroke-width="1.1"><circle cx="12.5" cy="12.5" r="6.5"/><ellipse cx="12.5" cy="12.5" rx="3" ry="6.5"/><path d="M6 12.5h13M7 9h11M7 16h11"/></g></svg>
    <span>www.cdlacombre.example</span>
  </div>
</main>
</body>
</html>
```